Heron Property Inspection business card

I am the principal inspector of Heron Property Inspections. I serve Northern Virginia from Winchester to Arlington.Associate, Federated Guild of Dwelling Examiners (FGDE)Graduate, FGDE Home Inspectors CourseNational Association of Home Inspectors ExamI'd like the business card to look more professional than comical.I pulled the attached picture off the web. I'd like to have something like that or an image of a house as my logo on the cards.

Target Market(s)

Persons who recently purchased a home.

Industry/Entity Type

Business

Contact Information for Business Card

Bob AllenBadger Home Inspections, LLC.4455 River RoadBluemont, Virginia 20135cell: 703-231-6680e-mail: tkmarlow@postvale.net

Font styles to use
Serif
Sans Serif

Requirements
Must have
• I'd like to have a logo, something that identifies me as a home inspector. The attached images are something that I'd like to have incorporated into my business card logo.
Nice to have
• I'd like a sketch of a house and/or a magnifying glass showing a house being inspected. The attached images are used as a suggestion only, I do not own the images.
Should not have
• Gimmicky stuff. I want to appear professional and trustworthy.

```html
<!DOCTYPE html>
<html lang="en">
<head>
<meta charset="utf-8">
<title>Heron Property Inspections – Business Card</title>
<link rel="stylesheet" href="https://fonts.googleapis.com/css2?family=Arvo:wght@700&family=Arimo:wght@400&display=swap">
<style>
  :root {
    --backdrop: #ecebe8;
    --card-white: #fbfbfb;
    --card-red: #c3222b;
    --card-red-deep: #a11a22;
    --accent-red: #c8262e;
    --ink-grey: #5a5a5a;
    --ink-white: #ffffff;
    --shadow: rgba(0, 0, 0, 0.18);
  }
  * { box-sizing: border-box; margin: 0; padding: 0; }
  html, body {
    width: 1200px;
    height: 892px;
    overflow: hidden;
    background: var(--backdrop);
  }
  .canvas {
    width: 1200px;
    height: 892px;
    display: flex;
    align-items: center;
    justify-content: center;
    gap: 48px;
  }
  .card {
    width: 540px;
    height: 309px;
    border-radius: 3px;
    box-shadow: 0 10px 28px var(--shadow);
    position: relative;
    overflow: hidden;
  }

  /* Front: brand lockup */
  .card-front {
    background: linear-gradient(160deg, #ffffff 0%, var(--card-white) 55%, #eeeeee 100%);
    display: flex;
    align-items: center;
    justify-content: center;
    gap: 18px;
    padding: 0 30px;
  }
  .brand-mark {
    flex: none;
    width: 58px;
    height: 58px;
    background: var(--accent-red);
  }
  .brand-name {
    font-family: "Arvo", Georgia, serif;
    font-weight: 700;
    color: var(--ink-grey);
    line-height: 1.2;
    white-space: nowrap;
  }
  .brand-name .owner { display: block; font-size: 31px; }
  .brand-name .company { display: block; font-size: 21px; margin-top: 4px; }

  /* Back: contact details */
  .card-back {
    background: linear-gradient(150deg, #d0333b 0%, var(--card-red) 40%, var(--card-red-deep) 100%);
    color: var(--ink-white);
    font-family: "Arimo", Arial, sans-serif;
    padding: 44px 46px 0 0;
    text-align: right;
  }
  .person-name { font-size: 36px; letter-spacing: -0.5px; line-height: 1; }
  .person-role { font-size: 19px; margin-top: 6px; }
  .contact-list {
    list-style: none;
    margin-top: 38px;
    font-size: 20px;
    line-height: 1.3;
  }
  .contact-list li { display: flex; justify-content: flex-end; align-items: center; gap: 12px; }
  .contact-icon {
    width: 26px;
    height: 22px;
    background: var(--ink-white);
    border-radius: 2px;
    display: inline-flex;
    align-items: center;
    justify-content: center;
  }
  .address { margin-top: 4px; padding-right: 38px; }
</style>
</head>
<body>
  <main class="canvas">
    <section class="card card-front" aria-label="Card front">
      <span class="brand-mark" aria-hidden="true"></span>
      <h1 class="brand-name">
        <span class="owner">Tim Marlow</span>
        <span class="company">Heron Property Inspections, LLC</span>
      </h1>
    </section>

    <section class="card card-back" aria-label="Card back">
      <p class="person-name">Employee Name</p>
      <p class="person-role">Your Position</p>
      <ul class="contact-list">
        <li>
          <span>703-555-0192</span>
          <span class="contact-icon">
            <svg width="16" height="16" viewBox="0 0 16 16" aria-hidden="true">
              <rect x="2" y="1" width="12" height="14" rx="2" fill="#222"/>
              <rect x="4" y="3" width="8" height="4" fill="#fff"/>
              <rect x="4" y="9" width="2" height="2" fill="#fff"/>
              <rect x="7" y="9" width="2" height="2" fill="#fff"/>
              <rect x="10" y="9" width="2" height="2" fill="#fff"/>
            </svg>
          </span>
        </li>
        <li>
          <span>tkmarlow@postvale.net</span>
          <span class="contact-icon">
            <svg width="18" height="14" viewBox="0 0 18 14" aria-hidden="true">
              <rect x="1" y="1" width="16" height="12" fill="#222"/>
              <path d="M1 1 L9 8 L17 1 M1 13 L7 6.5 M17 13 L11 6.5" stroke="#fff" stroke-width="1.4" fill="none"/>
            </svg>
          </span>
        </li>
        <li class="address">7182 Quarry Lane, Fernhill,</li>
        <li class="address">Virginia 20148</li>
      </ul>
    </section>
  </main>
</body>
</html>
```